New Business Card Design Project

We require a business card design for Vexalund, a newly established Indian company.
Our focus is on the development, manufacturing, and export of a diverse array of pharmaceutical products on a global scale. The card should convey a professional appearance, as our primary markets are in Africa, China, and Southeast Asian nations.
We envision a two-sided business card, with the reverse side dedicated to a logo set against a solid color or an elegantly designed pattern. The corners should be rounded. We would appreciate seeing both horizontal and vertical design options. We trust the designer to utilize their expertise in creating this design.

The content for the business card is included in the attached Word file.

Target Market(s)

Our primary markets are in Africa, China, and Southeast Asian, Latin America, Maldives, Sri Lanka

Industry/Entity Type

Pharmaceutical Manufacturing and Export

Contact Information for Business Card

Colors

Designer to choose colors to be used in the design.

Requirements
Must have
• The reverse side of the business card features solely the logo along with the tagline, "Wellness Beyond Borders."
Should not have
• The logo should not exceed two instances, encompassing both the front and back sides of the card.

```html
<!DOCTYPE html>
<html lang="en">
<head>
<meta charset="utf-8">
<title>Vexalund Business Card</title>
<link href="https://fonts.googleapis.com/css2?family=Montserrat:wght@700;800&family=Open+Sans:wght@400;600&family=Poppins:wght@400&display=swap" rel="stylesheet">
<style>
  :root {
    --stage: #232323;
    --brand-blue: #2ea6e1;
    --brand-blue-deep: #1b8fcc;
    --coral: #f0604d;
    --card-dark: #222328;
    --text-light: #f2f2f2;
  }
  * { margin: 0; padding: 0; box-sizing: border-box; }
  html, body {
    width: 1200px; height: 711px; overflow: hidden;
    background: var(--stage);
  }
  .stage {
    width: 1200px; height: 711px;
    display: flex; align-items: center; justify-content: center; gap: 40px;
  }
  .card {
    position: relative;
    width: 540px; height: 309px;
    border-radius: 22px;
    overflow: hidden;
    box-shadow: 0 14px 30px rgba(0,0,0,.55);
  }

  /* Reverse side */
  .card-back {
    background: var(--brand-blue);
    display: flex; flex-direction: column; align-items: center; justify-content: center;
  }
  .back-brand {
    display: flex; align-items: center; gap: 14px;
  }
  .back-brand .brand-dot {
    width: 26px; height: 26px; border-radius: 50%;
    background: var(--brand-blue-deep);
  }
  .back-brand .brand-name {
    font-family: "Montserrat", sans-serif; font-weight: 800;
    font-size: 58px; letter-spacing: -1px;
    color: var(--brand-blue-deep);
  }
  .tagline {
    margin-top: 12px;
    font-family: "Poppins", sans-serif; font-weight: 400;
    font-size: 14px; letter-spacing: .6px;
    color: #ffffff;
  }

  /* Front side */
  .card-front {
    background: var(--card-dark);
    border-bottom: 3px solid var(--brand-blue);
  }
  .front-brand {
    position: absolute; left: 34px; top: 52px;
    display: flex; align-items: center; gap: 10px;
  }
  .front-brand .brand-dot {
    width: 18px; height: 18px; border-radius: 50%;
    background: var(--coral);
  }
  .front-brand .brand-name {
    font-family: "Montserrat", sans-serif; font-weight: 800;
    font-size: 38px; letter-spacing: -.5px;
    color: var(--brand-blue);
  }
  .address {
    position: absolute; left: 36px; top: 118px;
    font-family: "Open Sans", sans-serif; font-size: 13px; line-height: 1.5;
    color: var(--text-light);
  }
  .contacts {
    position: absolute; left: 36px; bottom: 28px;
    list-style: none;
    font-family: "Open Sans", sans-serif; font-size: 13px; line-height: 1.65;
    color: var(--text-light);
  }
  .contacts li { display: flex; align-items: center; gap: 9px; }
  .contacts svg { width: 14px; height: 14px; flex: none; }

  .holder {
    position: absolute; right: 44px; top: 78px; text-align: right;
  }
  .holder-name {
    font-family: "Open Sans", sans-serif; font-size: 24px; white-space: nowrap;
  }
  .holder-name .first { color: var(--brand-blue); font-family: "Montserrat", sans-serif; font-weight: 700; }
  .holder-name .last { color: var(--coral); }
  .holder-role {
    font-family: "Open Sans", sans-serif; font-size: 13px;
    color: var(--text-light); margin-top: 2px;
  }
  .accent-bar {
    position: absolute; right: 0; top: 74px;
    width: 14px; height: 48px; background: var(--brand-blue);
  }
</style>
</head>
<body>
<main class="stage">
  <section class="card card-back" aria-label="Card reverse">
    <div class="back-brand">
      <span class="brand-dot"></span>
      <span class="brand-name">Vexalund</span>
    </div>
    <p class="tagline">Wellness Beyond Borders.</p>
  </section>

  <section class="card card-front" aria-label="Card front">
    <div class="front-brand">
      <span class="brand-dot"></span>
      <span class="brand-name">Vexalund</span>
    </div>
    <p class="address">12, Lotus Nagar,<br>Amrapur, 440117, India</p>

    <ul class="contacts">
      <li>
        <svg viewBox="0 0 14 14" aria-hidden="true"><rect x="3" y="1" width="8" height="12" rx="1.5" fill="none" stroke="#f0604d" stroke-width="1.4"/></svg>
        +91 98450 31726
      </li>
      <li>
        <svg viewBox="0 0 14 14" aria-hidden="true"><circle cx="7" cy="7" r="6" fill="none" stroke="#2ea6e1" stroke-width="1.4"/><ellipse cx="7" cy="7" rx="2.6" ry="6" fill="none" stroke="#2ea6e1" stroke-width="1"/><line x1="1" y1="7" x2="13" y2="7" stroke="#2ea6e1" stroke-width="1"/></svg>
        www.vexalund.com
      </li>
      <li>
        <svg viewBox="0 0 14 14" aria-hidden="true"><rect x="1" y="3" width="12" height="9" rx="1" fill="none" stroke="#f0604d" stroke-width="1.4"/><polyline points="1.5,3.5 7,8 12.5,3.5" fill="none" stroke="#f0604d" stroke-width="1.2"/></svg>
        rsontakke@vexalund.com
      </li>
    </ul>

    <div class="holder">
      <p class="holder-name"><span class="first">Ravi</span> <span class="last">K. Sontakke</span></p>
      <p class="holder-role">CEO</p>
    </div>
    <span class="accent-bar"></span>
  </section>
</main>
</body>
</html>
```